Lotstallmart.com Webpage Design

Design Brief for lotstallmart.com (Copy of Brief also in attached Word file)

Name of Website- lotstallmart.com (existing logo and look & feel of website to be changed)

Logo - Finalised. The logo files are attached with the brief as “logo.jpeg”. The “Blue- Grey” version of the logo is for use on lighter backgrounds and the “Orange-White” version of the logo is for use on darker backgrounds. (A full Black version of the logo is also attached). Both versions may be used in different parts of the website. All attached files are in .png format.
Status - The website in functional and is undergoing user trials. However, we want to improve the look & feel of the website so at it seems
a. cotemporary,
b. Easy to Navigate
c. professional and
d. Vibrant.

Please visit ‘lotstallmart.com’ to check out the website and its functionalities – please use it only as a reference for the features & functions to be provided, however the designer should use a ‘Free Hand’ in designing the composition of various parts of the webpage without getting too influenced by the existing design

Objective of the Website ‘lotstallmart.com –
a. It is a portal focussed on listing of ‘Retail’ specific real-estate properties by developers, owners and realty brokers. The properties shall listed under the following four categories-
i. Retail Malls
ii. Shopping Complexes
iii. High-street shops
iv. Retail Warehouses
*refer lotstallmart.com for better clarity

b. The abovementioned properties shall be listed either for ‘Sale’ or ‘rent\lease’ or both

c. Users shall visit the site in case they wish to acquire a retail \ shop space either on ‘sale’ or ‘rent’. These Users would be able to specify the ‘Search Criteria’ through the tool-bars provided on the website – the ‘Search Criteria’ shall comprise of ‘Type of space category’, ‘City’, ‘Locality’, transaction type ie ‘Rent \ Sale’ and ‘Area Range’

d. The main revenue model for the website shall be listing fee ( or advertising charges ) payable by those listing their properties on the website.

Three Main Pages of Website (lotstallmart.com) that need to be designed -
a. Main Home Page (visit the web link - http://lotstallmart.com/ ) - The main home page has the “Search Toolbar” for specifying of Search Criteria by the User. It shall also have the following features & functions-
i. Main Advertising Banner
ii. Featured Projects
iii. New Launches
iv. Toolbar with buttons – ‘Advertise with Us’, ‘Listings Alert’, ‘Mart Wizards’, ‘Advertiser Login’

b. Property Listings Page (visit the web link - http://lotstallmart.com/gurgaon-in-india ) - The List of property options that match the Criteria specified by the ‘User’ get displayed on this page.

c. Property Detail Page - When the ‘User’ clicks on the “More….” Button on the ‘Property Listings Page’ (given in point b. above) the web page with the details of the property opens. (For Example – visit the web link - http://lotstallmart.com/vorne-Shopping-Complex-vorne-quadrion-gurgaon-636 )

Note:- Please refer to attached ‘Shopping’ related images the designer may use them on the website to provide a look & feel of retail if required – either separately or rotate in a single window

Target Market(s)

Retailers & Investors looking for retail space, Real Estate Brokers, Developers

Industry/Entity Type

Advertising

Number of Pages Required

3 page

Requirements
Must have
• Refer to existing site lotstallmart.com -- all the existing functionalities are a must have.
Nice to have
• The Designer may use the retail related images on the website if required for making it more vibrant. Refer attached images Shopping(1-6).jpg

```html
<!DOCTYPE html>
<html lang="en">
<head>
<meta charset="utf-8">
<title>Lotstallmart.com – Retail Space Portal</title>
<link href="https://fonts.googleapis.com/css2?family=Open+Sans:ital,wght@0,300;0,400;0,600;0,700;1,400&display=swap" rel="stylesheet">
<style>
:root{
  --ink:#222;
  --muted:#666;
  --blue:#1a8fe0;
  --blue-dark:#0d72c2;
  --orange:#e9a036;
  --tag:#f7890f;
  --dark:#262626;
  --pale:#eaf5fd;
  --line:#c9c9c9;
  --field:#fff;
  --grey-btn:#4a4a4a;
}
*{box-sizing:border-box;margin:0;padding:0}
html,body{width:1200px;height:2550px;overflow:hidden}
body{font-family:"Open Sans",Arial,sans-serif;color:var(--ink);background:#fff;font-size:13px;position:relative}
.wrap{width:980px;margin:0 auto;position:relative;height:100%}

/* top bar */
.topbar{height:25px;background:var(--dark);color:#cfcfcf;font-size:11.5px}
.topbar .wrap{display:flex;align-items:center;justify-content:space-between}
.city-list{display:flex}
.city-list span{padding:0 8px;border-right:1px solid #666;line-height:12px}
.city-list span:first-child{padding-left:0}
.city-list span:last-child{border-right:0}
.login-link{color:#fff;text-decoration:underline;font-weight:600}

/* header */
.header{height:114px}
.header .wrap{display:flex;align-items:center}
.brand{display:flex;align-items:center;gap:8px;width:300px}
.brand-dot{width:34px;height:34px;border-radius:50%;background:var(--blue)}
.brand-name{font-size:29px;font-weight:700;color:var(--blue);line-height:1;letter-spacing:-.5px}
.brand-tag{font-size:7.5px;color:#555;font-weight:600;letter-spacing:.3px;margin-top:3px}
.main-nav{display:flex;height:70px}
.nav-item{padding:0 18px;border-right:1px solid #ddd;display:flex;flex-direction:column;justify-content:center}
.nav-item:last-child{border-right:0}
.nav-item strong{font-size:16px;font-weight:600;color:#333}
.nav-item small{font-size:11.5px;color:#888}
.list-btn{margin-left:auto;background:var(--blue);color:#fff;font-weight:700;font-size:15px;width:169px;height:38px;display:flex;align-items:center;justify-content:center;border-bottom:3px solid var(--blue-dark)}

/* hero */
.hero{height:475px;background:linear-gradient(100deg,#4a3f37 0%,#7a6a5a 30%,#5d4b3c 55%,#8b7b6d 80%,#3f3a35 100%);position:relative}
.hero h1{position:absolute;left:204px;top:222px;font-size:46px;font-weight:300;color:#fff;letter-spacing:.5px;line-height:62px}
.hero h1 b{font-weight:700}

/* search */
.search-band{height:120px;background:var(--orange);padding-top:12px}
.search-row{display:flex;gap:6px;margin-left:14px}
.search-field label{display:block;font-size:11.5px;color:#fff;font-weight:600;margin-bottom:4px}
.select-box{height:33px;background:var(--field);font-size:11.5px;color:#555;padding:0 10px;display:flex;align-items:center;justify-content:space-between}
.select-box::after{content:"";border:4px solid transparent;border-top-color:#666;margin-top:4px}
.input-box{height:33px;background:var(--field);font-size:11.5px;color:#666;padding:0 10px;display:flex;align-items:center}
.search-btn{margin-top:19px;width:152px;height:33px;background:var(--grey-btn);color:#fff;font-weight:700;font-size:19px;display:flex;align-items:center;justify-content:center}
.format-row{display:flex;gap:28px;margin:10px 0 0 14px;font-size:11.5px;color:#fff;font-weight:600;align-items:center}
.format-row .check{display:flex;align-items:center;gap:6px}
.format-row .check i{width:10px;height:10px;background:#fff;border:1px solid #bbb}
.format-row .meaning b{color:#3a2a10}

/* categories */
.categories{height:235px;position:relative}
.cat{position:absolute;top:38px;width:220px;margin-left:-110px;text-align:center}
.cat svg{width:58px;height:58px;display:block;margin:0 auto}
.cat h3{font-size:19px;font-weight:600;color:#333;margin-top:2px}
.cat p{font-size:12px;color:#555}
.cat.active h3{color:var(--blue)}
.track{position:absolute;left:128px;right:110px;top:204px;height:6px;background:var(--line)}
.knot{position:absolute;top:191px;width:32px;height:32px;margin-left:-16px;border-radius:50%;background:#fff;border:4px solid var(--line)}
.knot.active{border-color:var(--blue)}
.knot.active::after{content:"";position:absolute;inset:5px;border-radius:50%;background:var(--blue)}

/* section headings */
.sec-head{position:relative;text-align:center;height:70px}
.sec-head::before{content:"";position:absolute;left:0;right:0;top:14px;height:1px;background:#333}
.sec-head h2{display:inline-block;position:relative;padding:0 18px;font-size:22px;font-weight:600;color:#222;letter-spacing:.3px;line-height:28px}
.sec-head em{display:block;font-size:11.5px;color:#666;font-style:italic}
.sec-arrows{position:absolute;right:0;top:8px;display:flex;gap:2px}
.sec-arrows span{width:14px;height:13px;background:#333;display:flex;align-items:center;justify-content:center}
.projects .sec-head h2{background:#fff}
.launches .sec-head h2{background:var(--pale)}

/* featured projects */
.projects{padding-top:70px;height:517px}
.card-row{display:flex;gap:12px;margin-top:16px}
.proj-card{width:187px;height:325px;box-shadow:0 0 4px rgba(0,0,0,.25);background:#fff}
.proj-photo{height:200px;position:relative}
.p1{background:linear-gradient(160deg,#7fa8c6,#c9b79a 55%,#8a5a3a)}
.p2{background:linear-gradient(170deg,#2c4a78,#5f6f8c 50%,#c48a4a)}
.p3{background:linear-gradient(170deg,#c8d4c4,#8aa290 50%,#5f6f60)}
.p4{background:linear-gradient(170deg,#b9d2e0,#9fa8a4 50%,#6d6f6a)}
.p5{background:linear-gradient(170deg,#8c8aa3,#c59a86 50%,#6a5a50)}
.city-tag{position:absolute;right:4px;bottom:4px;background:var(--tag);color:#fff;font-weight:600;font-size:13px;width:76px;height:26px;display:flex;align-items:center;justify-content:center}
.proj-info{padding:10px 8px 0}
.proj-info h4{font-size:15px;font-weight:700;color:#333}
.proj-info .loc{font-size:11.5px;color:var(--blue);margin-top:1px}
.proj-info .type{font-size:11.5px;color:#222;margin-top:5px;padding-bottom:8px;border-bottom:1px dotted #aaa}
.view-btn{margin-top:8px;height:26px;background:var(--blue);color:#fff;font-weight:600;font-size:13px;display:flex;align-items:center;justify-content:center}

/* launches */
.launches{height:350px;background:var(--pale);padding-top:36px}
.launch-row{display:flex;justify-content:space-between;padding:0 9px;margin-top:22px}
.launch-card{width:293px;height:172px;background:linear-gradient(180deg,#1f2a38,#34404f 60%,#222a33);text-align:center;color:#fff;padding-top:14px}
.launch-card .city{font-size:16px}
.launch-card .title{font-size:22px;color:#2e9bef;font-weight:600;line-height:32px}
.launch-card .sector{font-size:14px}
.launch-card .type{font-size:14px;color:#2e9bef;margin-top:8px}
.launch-card .cta{font-size:14px;font-weight:700;text-decoration:underline;margin-top:9px}

/* info columns */
.info{height:379px;padding-top:30px}
.info .wrap{display:flex}
.col h3{font-size:18px;font-weight:700;color:#222;margin-bottom:8px}
.col p{font-size:12px;line-height:18px;color:#333}
.col-alert{width:294px;margin-left:12px}
.col-editor{width:316px;margin-left:38px}
.col-wizard{width:293px;margin-left:32px}
.field{height:32px;background:#f1f1f1;border:1px solid #e2e2e2;font-size:12px;color:#444;padding:0 10px;display:flex;align-items:center;margin-top:9px}
.field.blue{color:var(--blue)}
.field.tall{height:66px;align-items:flex-start;padding-top:7px}
.hint{font-size:11.5px;color:#555;margin-top:8px}
.grey-btn{width:126px;height:34px;background:linear-gradient(#efefef,#cfcfcf);border:1px solid #bbb;font-weight:700;font-size:16px;color:#333;display:flex;align-items:center;justify-content:center;margin-top:14px}
.editor-photo{height:108px;background:linear-gradient(180deg,#d6dde4,#8d9aa6 45%,#4a4f57);margin:2px 0 14px}
.read-btn{width:124px;height:36px;background:var(--blue);color:#fff;font-weight:600;font-size:16px;display:flex;align-items:center;justify-content:center;margin:10px 0 0 190px}

/* footer */
.footer{height:335px;background:var(--dark);color:#ddd;padding-top:26px}
.foot-cols{display:flex}
.foot-cols h3{font-size:20px;font-weight:600;color:#fff;margin-bottom:12px}
.foot-about{width:310px;margin-left:5px}
.foot-links{display:flex;gap:42px;font-size:12px;line-height:20px}
.foot-site{width:360px;font-size:12px;line-height:21px}
.foot-contact{margin-left:95px;font-size:12px;line-height:20px}
.socials{display:flex;gap:4px;margin-top:10px}
.socials span{width:22px;height:22px}
.s1{background:#3b5998}.s2{background:#2aa9e0}.s3{background:#cc2222}.s4{background:#d34836}.s5{background:#1d7bb5}
.foot-brand{position:absolute;right:0;top:250px;display:flex;align-items:center;gap:8px}
.foot-brand i{width:30px;height:30px;border-radius:50%;background:#8a8a8a}
.foot-brand span{font-size:24px;font-weight:700;color:#9a9a9a}
.copyright{position:absolute;left:5px;top:262px;font-size:11.5px;color:#eee}
.copyright .legal{margin-top:10px;color:#ccc}
.copyright .legal b{color:var(--orange);font-weight:400}
</style>
</head>
<body>

<div class="topbar">
  <div class="wrap">
    <div class="city-list"><span>Bangalore</span><span>Chennai</span><span>Greater Noida</span><span>Gurgaon</span><span>Hyderabad</span><span>Jaipur</span><span>Khanna</span><span>Kolkatta</span><span>Mumbai</span><span>Noida</span><span>Pune</span><span>Surat</span></div>
    <div class="login-link">Advetise Login</div>
  </div>
</div>

<header class="header">
  <div class="wrap">
    <div class="brand">
      <div class="brand-dot"></div>
      <div>
        <div class="brand-name">lotstallmart</div>
        <div class="brand-tag">INDIA'S LEADING PORTAL FOR RETAIL SPACE</div>
      </div>
    </div>
    <nav class="main-nav">
      <div class="nav-item"><strong>ADVERTISE WITH US</strong><small>Standard listing - FREE</small></div>
      <div class="nav-item"><strong>MART WIZARDS</strong><small>Shop Search Services</small></div>
      <div class="nav-item"><strong>LISTING ALERT</strong><small>&nbsp;</small></div>
    </nav>
    <div class="list-btn">List YourProperty</div>
  </div>
</header>

<section class="hero" role="img" aria-label="Photo of young shoppers with bags walking through a mall">
  <h1>VERANO 12 CITY <b>WALK NOIDA</b></h1>
</section>

<section class="search-band">
  <div class="wrap">
    <div class="search-row">
      <div class="search-field" style="width:194px"><label>Sale Or Rent Or Both:</label><div class="select-box">Both</div></div>
      <div class="search-field" style="width:194px"><label>Select City:</label><div class="select-box">Select</div></div>
      <div class="search-field" style="width:193px"><label>Select Locality / Micro - Market:</label><div class="select-box">Select</div></div>
      <div class="search-field" style="width:196px"><label>Enter Keywords:</label><div class="input-box">Name of Project , Developer etc</div></div>
      <div class="search-btn">SEARCH</div>
    </div>
    <div class="format-row">
      <div class="check"><i></i>Retail Malls</div>
      <div class="check"><i></i>Retail Warehouses</div>
      <div class="check"><i></i>Shopping Complex</div>
      <div class="check"><i></i>High Street Shops</div>
      <div class="meaning">Select Retail Format: <b>Meaning of Retail Format</b></div>
    </div>
  </div>
</section>

<section class="categories">
  <div class="wrap">
    <div class="cat active" style="left:128px">
      <svg viewBox="0 0 58 58"><rect x="10" y="16" width="34" height="22" rx="3" fill="#1a8fe0" transform="rotate(-20 27 27)"/><rect x="16" y="22" width="34" height="22" rx="3" fill="#3aa6ef" transform="rotate(15 33 33)"/><circle cx="33" cy="33" r="5" fill="#fff"/></svg>
      <h3>Retail Malls</h3><p>Centrally Air-Conditioned</p>
    </div>
    <div class="cat" style="left:354px">
      <svg viewBox="0 0 58 58"><path d="M12 22h34l-3 28H15z" fill="#333"/><path d="M21 24v-7a8 8 0 0 1 16 0v7" fill="none" stroke="#333" stroke-width="3"/></svg>
      <h3>High Street Shops</h3><p>Road Facing Retail</p>
    </div>
    <div class="cat" style="left:589px">
      <svg viewBox="0 0 58 58"><path d="M6 30 24 14l18 16H36v18H12V30z" fill="#333"/><path d="M24 14 36 4l18 16h-6v18H40" fill="#555"/><rect x="20" y="36" width="8" height="12" fill="#fff"/></svg>
      <h3>Retail Warehouses</h3><p>Back-end Ratail Storage</p>
    </div>
    <div class="cat" style="left:830px">
      <svg viewBox="0 0 58 58" fill="#333"><rect x="10" y="20" width="12" height="32"/><rect x="22" y="8" width="16" height="44"/><rect x="38" y="16" width="12" height="36"/><g fill="#fff"><rect x="26" y="13" width="3" height="3"/><rect x="31" y="13" width="3" height="3"/><rect x="26" y="20" width="3" height="3"/><rect x="31" y="20" width="3" height="3"/><rect x="26" y="27" width="3" height="3"/><rect x="31" y="27" width="3" height="3"/><rect x="13" y="25" width="3" height="3"/><rect x="41" y="22" width="3" height="3"/><rect x="13" y="32" width="3" height="3"/><rect x="41" y="29" width="3" height="3"/></g></svg>
      <h3>Shopping Complex</h3><p>Non Air-Conditioned Building</p>
    </div>
    <div class="track"></div>
    <div class="knot active" style="left:128px"></div>
    <div class="knot" style="left:354px"></div>
    <div class="knot" style="left:589px"></div>
    <div class="knot" style="left:830px"></div>
  </div>
</section>

<section class="projects">
  <div class="wrap" style="height:auto">
    <div class="sec-head">
      <h2>FEATURED RETAIL PROJECTS</h2><em>Across India</em>
      <div class="sec-arrows"><span><svg width="6" height="7"><path d="M5 0 0 3.5 5 7z" fill="#fff"/></svg></span><span><svg width="6" height="7"><path d="M1 0 6 3.5 1 7z" fill="#fff"/></svg></span></div>
    </div>
    <div class="card-row">
      <article class="proj-card"><div class="proj-photo p1" role="img" aria-label="Photo of a modern shopping mall exterior"><span class="city-tag">Surat</span></div><div class="proj-info"><h4>ORVANTA</h4><div class="loc">Althan</div><div class="type">Shopping Complex</div><div class="view-btn">View the listing</div></div></article>
      <article class="proj-card"><div class="proj-photo p2" role="img" aria-label="Photo of a commercial tower at dusk"><span class="city-tag">Surat</span></div><div class="proj-info"><h4>ORVANTA</h4><div class="loc">Althan</div><div class="type">Shopping Complex</div><div class="view-btn">View the listing</div></div></article>
      <article class="proj-card"><div class="proj-photo p3" role="img" aria-label="Photo of a mall atrium with palm trees"><span class="city-tag">Surat</span></div><div class="proj-info"><h4>ORVANTA</h4><div class="loc">Althan</div><div class="type">Shopping Complex</div><div class="view-btn">View the listing</div></div></article>
      <article class="proj-card"><div class="proj-photo p4" role="img" aria-label="Photo of an open-air retail plaza"><span class="city-tag">Surat</span></div><div class="proj-info"><h4>ORVANTA</h4><div class="loc">Althan</div><div class="type">Shopping Complex</div><div class="view-btn">View the listing</div></div></article>
      <article class="proj-card"><div class="proj-photo p5" role="img" aria-label="Photo of a retail complex at sunset"><span class="city-tag">Surat</span></div><div class="proj-info"><h4>ORVANTA</h4><div class="loc">Althan</div><div class="type">Shopping Complex</div><div class="view-btn">View the listing</div></div></article>
    </div>
  </div>
</section>

<section class="launches">
  <div class="wrap" style="height:auto">
    <div class="sec-head">
      <h2>FEATURED NEW LAUNCHES</h2><em>Across India</em>
      <div class="sec-arrows"><span><svg width="6" height="7"><path d="M5 0 0 3.5 5 7z" fill="#fff"/></svg></span><span><svg width="6" height="7"><path d="M1 0 6 3.5 1 7z" fill="#fff"/></svg></span></div>
    </div>
    <div class="launch-row">
      <article class="launch-card" role="img" aria-label="Dark photo of a high street retail project"><div class="city">Karnal</div><div class="title">Kavel 34 Market Square</div><div class="sector">Sector - 34</div><div class="type">Shopping Complex</div><div class="cta">VIEW THE LISTING</div></article>
      <article class="launch-card" role="img" aria-label="Dark photo of a high street retail project"><div class="city">Karnal</div><div class="title">Kavel 34 Market Square</div><div class="sector">Sector - 34</div><div class="type">Shopping Complex</div><div class="cta">VIEW THE LISTING</div></article>
      <article class="launch-card" role="img" aria-label="Dark photo of a high street retail project"><div class="city">Karnal</div><div class="title">Kavel 34 Market Square</div><div class="sector">Sector - 34</div><div class="type">Shopping Complex</div><div class="cta">VIEW THE LISTING</div></article>
    </div>
  </div>
</section>

<section class="info">
  <div class="wrap">
    <div class="col col-alert">
      <h3>Listing Alert</h3>
      <p>Suscribe &nbsp;for Fortnightly Email update on New Listings @ lotstallmart</p>
      <div class="field">Enter your email address:</div>
      <div class="field blue">Select options</div>
      <div class="hint">(select retail format of interest)</div>
      <div class="field">Adilabad</div>
      <div class="hint">(select cities of interest)</div>
      <div class="grey-btn">Subscribe</div>
    </div>
    <div class="col col-editor">
      <h3>Editor’s Choice</h3>
      <div class="editor-photo" role="img" aria-label="Photo of a mall interior corridor with shops"></div>
      <p>A "Select" Listing of Retail Properties Handpicked by our Editors based on their own positive evaluation on parameters &amp; attributes such as Design Concept, Location Developer, Success Potential. So Read On to Check Out for yourself ........ ..</p>
      <div class="read-btn">Read More</div>
    </div>
    <div class="col col-wizard">
      <h3>Mart Wizards</h3>
      <p>Post your Retail Space requirement with us and our experts shall get back with suitable options and even help you in your transaction. This is a Free Service!</p>
      <div class="field">Enter your email address:</div>
      <div class="field">Your Mobile No</div>
      <div class="field tall">Add Description of Requirement</div>
      <div class="grey-btn" style="margin-left:167px">Send</div>
    </div>
  </div>
</section>

<footer class="footer">
  <div class="wrap">
    <div class="foot-cols">
      <div class="foot-about">
        <h3>About Mart Central</h3>
        <div class="foot-links">
          <div>About Us<br>Privacy Policy<br>Terms of Use<br>Contact Us<br>Site Map</div>
          <div>Retail Malls<br>Shopping Complex<br>High Street Shops<br>Retail Warehouses</div>
        </div>
      </div>
      <div class="foot-site">
        <h3>www.lotstallmart.com</h3>
        Lotstallmart.com - About Us Lotstallmart.com is a Specialised Web based platform for Retail Space, featuring properties across India under various formats such as Retail Malls, Shopping Complexes, High-street Shops. Also featured are Retail Warehouses which provide the logistic back-end for the retail business. Lotstallmart.com is useful to various category of users as follows- a. Devel
      </div>
      <div class="foot-contact">
        <h3>Contact Us</h3>
        Mart Central<br>Unit 218, 2nd Floor,<br>Lorem Ipsum is simply,<br>Sector-x, Gurgaon - 122002<br>
        <div style="margin-top:8px">Phone : 000-000-0000<br>Fax : 000 - 000 - 0000</div>
        <div class="socials"><span class="s1"></span><span class="s2"></span><span class="s3"></span><span class="s4"></span><span class="s5"></span></div>
      </div>
    </div>
    <div class="copyright">
      Copyright © 2013 Mart Central Hub.com. All rights reserved.
      <div class="legal"><b>Privacy Policy</b> &nbsp;| &nbsp;Terms of Use</div>
    </div>
    <div class="foot-brand"><i></i><span>lotstallmart</span></div>
  </div>
</footer>

</body>
</html>
```